Create Premium Wine Label Design

We are premium wine exporters from Australia. We are looking to introduce new brand " The Velmora" - in red wine, White wine and Sparkling wine to international market.

The sample label design for red wine ( Shiraz) is attached.

This is our luxury brand. We need a stunning wine label designs for (front, back and neck) that should be mostly in GOLD colour and design should be really eye catching.

We have provided sample design for front, back and neck labels. However, we are looking forward to see a completely new improvised design.

LOGO attached.

Front Label Design Specification:

* We would like to see designs that are in Gold colour.
* Wine Bottle size is standard: 750ml; we assume the same design can be resizable to different bottle sizes.
* Our design should suit both black, white and sparkling wine bottles(sample attached)
* Use our logo in the design (see attached - label sample)
* Content for front label (see attached).
* Design should include all information specified in the sample

Back Label Design
* All contents in the sample should be used ( sample attached)
* LOGO attached.

Neck Label Design
* Sample of Neck label attached, please provide similar or your own design.
* LOGO attached.

Image Samples:
* Samples of label designs we like (see attached)
* Sample for gold color (see attached)
* For bottle shapes (see attached)
* Front, Back and Neck Label Samples (see attached)

Target Market(s)

International Wine Market

Font styles to use
Decorative
Script

Requirements
Must have
• Must have golden color on front and back label

```html
<!DOCTYPE html>
<html lang="en">
<head>
<meta charset="utf-8">
<title>Solvarra Shiraz — The Velmora label set</title>
<link href="https://fonts.googleapis.com/css2?family=Cinzel:wght@400;700&family=Cinzel+Decorative:wght@700;900&family=Roboto+Condensed:wght@400;700&display=swap" rel="stylesheet">
<style>
  :root{
    --gold:#d4ad4a;
    --gold-light:#f3dc86;
    --gold-deep:#a27a22;
    --green:#0e3323;
    --green-deep:#082116;
    --cream:#f5f2e8;
    --cream-shade:#e4e0d4;
    --black:#0b0b0b;
    --black-soft:#222;
    --grey-lace:#8d8d8d;
    --canvas:#ffffff;
    --gold-grad:linear-gradient(180deg,var(--gold-light) 0%,var(--gold) 45%,var(--gold-deep) 100%);
  }
  *{box-sizing:border-box;margin:0;padding:0}
  html,body{width:1200px;height:1200px;overflow:hidden;background:var(--canvas)}
  .sheet{position:relative;width:1200px;height:1200px;font-family:"Roboto Condensed",sans-serif}

  /* colour themes */
  .theme-green{--bg:var(--green);--bg-edge:var(--green-deep);--lace:#2f5a45;--ink:#e9e4d2;--year:#ffffff}
  .theme-cream{--bg:var(--cream);--bg-edge:var(--cream-shade);--lace:#c9c9c4;--ink:#222;--year:#111111}
  .theme-black{--bg:var(--black);--bg-edge:var(--black-soft);--lace:#3a3a3a;--ink:#e6e6e6;--year:#ffffff}

  .gold-text{background:var(--gold-grad);-webkit-background-clip:text;background-clip:text;color:transparent}

  /* front labels */
  .front-row{position:absolute;top:70px;left:0;width:1200px;display:flex;justify-content:center;gap:90px}
  .front-label{position:relative;width:260px;height:360px;background:var(--bg);
    box-shadow:0 8px 24px rgba(0,0,0,.18);display:flex;flex-direction:column;align-items:center;padding-top:26px}
  .brand{display:flex;align-items:center;gap:7px}
  .brand-dot{width:14px;height:14px;border-radius:50%;background:var(--gold)}
  .brand-name{font-family:"Cinzel",serif;font-weight:700;color:var(--gold);font-size:17px;letter-spacing:1.5px}
  .flourish{width:70px;height:8px;margin-top:6px;border-radius:4px;background:var(--gold);opacity:.7}
  .lace-medallion{position:relative;width:190px;height:190px;margin-top:12px;border-radius:50%;
    background:radial-gradient(circle,var(--lace) 0%,var(--bg) 72%);
    display:flex;flex-direction:column;align-items:center;justify-content:center}
  .varietal{font-family:"Roboto Condensed",sans-serif;font-weight:700;font-size:16px;letter-spacing:1px}
  .title{display:flex;align-items:center;gap:4px;margin-top:4px}
  .title-the{font-family:"Cinzel",serif;font-weight:700;font-size:9px;writing-mode:vertical-rl;transform:rotate(180deg);letter-spacing:1px}
  .title-name{font-family:"Cinzel Decorative",serif;font-weight:900;font-size:27px;letter-spacing:.5px}
  .vintage{font-family:"Cinzel",serif;font-weight:700;font-size:20px;color:var(--year);margin-top:6px}
  .origin-band{position:absolute;left:0;right:0;bottom:22px;height:24px;background:var(--gold-grad);
    display:flex;align-items:center;justify-content:center;
    font-family:"Cinzel",serif;font-weight:700;font-size:12px;letter-spacing:1px;color:var(--black)}
  .theme-green .origin-band,.theme-black .origin-band{color:var(--green-deep)}
  .theme-black .origin-band{color:var(--black)}

  /* back labels */
  .back-row{position:absolute;top:500px;left:0;width:1200px;display:flex;justify-content:center;gap:70px}
  .back-label{position:relative;width:300px;height:420px;background:var(--bg);
    box-shadow:0 8px 24px rgba(0,0,0,.18);overflow:hidden}
  .lace-field{position:absolute;left:0;top:0;width:300px;height:200px;
    background:linear-gradient(180deg,var(--lace) 0%,var(--bg) 100%)}
  .back-heading{position:absolute;top:30px;left:0;width:100%;display:flex;flex-direction:column;align-items:center}
  .back-heading .varietal{font-size:26px}
  .back-heading .title-name{font-size:38px}
  .back-heading .title-the{font-size:12px}
  .rule{position:absolute;left:40px;right:40px;height:1px;background:var(--gold)}
  .rule-top{top:175px}
  .rule-bottom{top:255px}
  .tasting-note{position:absolute;top:183px;left:30px;right:30px;font-size:7.6px;line-height:1.4;color:var(--ink);text-align:center}
  .tasting-note strong{color:var(--gold);font-weight:700}
  .legal{position:absolute;top:268px;left:18px;right:14px;height:140px}
  .legal-brand{position:absolute;left:8px;top:60px;display:flex;align-items:center;gap:5px}
  .legal-brand .brand-name{font-size:11px;letter-spacing:1px}
  .legal-brand .brand-dot{width:9px;height:9px}
  .legal-info{position:absolute;left:140px;top:0;width:140px;color:var(--ink);font-size:6.6px;line-height:1.35}
  .legal-info h3{font-size:8px;font-weight:700;margin-bottom:5px}
  .legal-info p{margin-bottom:6px}
  .volume{font-size:10px;font-weight:700;margin-top:2px}
  .abv{position:absolute;left:140px;top:108px;font-size:6.5px;font-weight:700;color:var(--ink);writing-mode:vertical-rl;transform:rotate(180deg)}
  .glass-badge{position:absolute;left:160px;top:104px;width:26px;height:28px;background:#fff;display:flex;align-items:center;justify-content:center}
</style>
</head>
<body>
<main class="sheet">

  <section class="front-row" aria-label="Front labels">
    <article class="front-label theme-green">
      <div class="brand"><span class="brand-dot"></span><span class="brand-name">SOLVARRA</span></div>
      <div class="flourish" role="img" aria-label="Gold scroll ornament"></div>
      <div class="lace-medallion" role="img" aria-label="Lace mandala ornament behind the wine name">
        <span class="varietal gold-text">SHIRAZ</span>
        <div class="title"><span class="title-the gold-text">THE</span><span class="title-name gold-text">VELMORA</span></div>
        <span class="vintage">2018</span>
      </div>
      <div class="origin-band">WINE OF AUSTRALIA</div>
    </article>

    <article class="front-label theme-cream">
      <div class="brand"><span class="brand-dot"></span><span class="brand-name">SOLVARRA</span></div>
      <div class="flourish" role="img" aria-label="Gold scroll ornament"></div>
      <div class="lace-medallion" role="img" aria-label="Lace mandala ornament behind the wine name">
        <span class="varietal gold-text">SHIRAZ</span>
        <div class="title"><span class="title-the gold-text">THE</span><span class="title-name gold-text">VELMORA</span></div>
        <span class="vintage">2018</span>
      </div>
      <div class="origin-band">WINE OF AUSTRALIA</div>
    </article>

    <article class="front-label theme-black">
      <div class="brand"><span class="brand-dot"></span><span class="brand-name">SOLVARRA</span></div>
      <div class="flourish" role="img" aria-label="Gold scroll ornament"></div>
      <div class="lace-medallion" role="img" aria-label="Lace mandala ornament behind the wine name">
        <span class="varietal gold-text">SHIRAZ</span>
        <div class="title"><span class="title-the gold-text">THE</span><span class="title-name gold-text">VELMORA</span></div>
        <span class="vintage">2018</span>
      </div>
      <div class="origin-band">WINE OF AUSTRALIA</div>
    </article>
  </section>

  <section class="back-row" aria-label="Back labels">
    <article class="back-label theme-green">
      <div class="lace-field" role="img" aria-label="Floral lace pattern"></div>
      <div class="back-heading">
        <span class="varietal gold-text">SHIRAZ</span>
        <div class="title"><span class="title-the gold-text">THE</span><span class="title-name gold-text">VELMORA</span></div>
      </div>
      <div class="rule rule-top"></div>
      <p class="tasting-note"><strong>Solvarra Shiraz — The Velmora</strong> is a classic fruit driven wine bursting with aromas of dark fruits and spice with background notes of charred French oak. This is a full bodied wine showcasing rich and juicy dark fruits of plum and cherry balanced with soft tannins and oak, providing a long lasting finish. This wine matches perfectly with a range of rich and hearty red meat or pasta dishes.</p>
      <div class="rule rule-bottom"></div>
      <div class="legal">
        <div class="legal-brand"><span class="brand-dot"></span><span class="brand-name">SOLVARRA</span></div>
        <div class="legal-info">
          <h3>Product of Australia</h3>
          <p>Preservative (220) Antioxidant (300)<br>May Contain Traces of Milk<br>Country of Origin : Australia</p>
          <p>Solvarra Wines Pty. Ltd.,<br>Eastmere<br>Victoria, Australia</p>
          <div class="volume">750 mL</div>
        </div>
        <span class="abv">12.5% Alc</span>
        <div class="glass-badge"><svg width="12" height="20" viewBox="0 0 12 20" aria-label="Wine glass"><path d="M1 1h10c0 5-2 8-5 8S1 6 1 1z" fill="#9b1b2a"/><path d="M6 9v8M3 19h6" stroke="#333" stroke-width="1.2" fill="none"/></svg></div>
      </div>
    </article>

    <article class="back-label theme-cream">
      <div class="lace-field" role="img" aria-label="Floral lace pattern"></div>
      <div class="back-heading">
        <span class="varietal gold-text">SHIRAZ</span>
        <div class="title"><span class="title-the gold-text">THE</span><span class="title-name gold-text">VELMORA</span></div>
      </div>
      <div class="rule rule-top"></div>
      <p class="tasting-note"><strong>Solvarra Shiraz — The Velmora</strong> is a classic fruit driven wine bursting with aromas of dark fruits and spice with background notes of charred French oak. This is a full bodied wine showcasing rich and juicy dark fruits of plum and cherry balanced with soft tannins and oak, providing a long lasting finish. This wine matches perfectly with a range of rich and hearty red meat or pasta dishes.</p>
      <div class="rule rule-bottom"></div>
      <div class="legal">
        <div class="legal-brand"><span class="brand-dot"></span><span class="brand-name">SOLVARRA</span></div>
        <div class="legal-info">
          <h3>Product of Australia</h3>
          <p>Preservative (220) Antioxidant (300)<br>May Contain Traces of Milk<br>Country of Origin : Australia</p>
          <p>Solvarra Wines Pty. Ltd.,<br>Eastmere<br>Victoria, Australia</p>
          <div class="volume">750 mL</div>
        </div>
        <span class="abv">12.5% Alc</span>
        <div class="glass-badge"><svg width="12" height="20" viewBox="0 0 12 20" aria-label="Wine glass"><path d="M1 1h10c0 5-2 8-5 8S1 6 1 1z" fill="#9b1b2a"/><path d="M6 9v8M3 19h6" stroke="#333" stroke-width="1.2" fill="none"/></svg></div>
      </div>
    </article>

    <article class="back-label theme-black">
      <div class="lace-field" role="img" aria-label="Floral lace pattern"></div>
      <div class="back-heading">
        <span class="varietal gold-text">SHIRAZ</span>
        <div class="title"><span class="title-the gold-text">THE</span><span class="title-name gold-text">VELMORA</span></div>
      </div>
      <div class="rule rule-top"></div>
      <p class="tasting-note"><strong>Solvarra Shiraz — The Velmora</strong> is a classic fruit driven wine bursting with aromas of dark fruits and spice with background notes of charred French oak. This is a full bodied wine showcasing rich and juicy dark fruits of plum and cherry balanced with soft tannins and oak, providing a long lasting finish. This wine matches perfectly with a range of rich and hearty red meat or pasta dishes.</p>
      <div class="rule rule-bottom"></div>
      <div class="legal">
        <div class="legal-brand"><span class="brand-dot"></span><span class="brand-name">SOLVARRA</span></div>
        <div class="legal-info">
          <h3>Product of Australia</h3>
          <p>Preservative (220) Antioxidant (300)<br>May Contain Traces of Milk<br>Country of Origin : Australia</p>
          <p>Solvarra Wines Pty. Ltd.,<br>Eastmere<br>Victoria, Australia</p>
          <div class="volume">750 mL</div>
        </div>
        <span class="abv">12.5% Alc</span>
        <div class="glass-badge"><svg width="12" height="20" viewBox="0 0 12 20" aria-label="Wine glass"><path d="M1 1h10c0 5-2 8-5 8S1 6 1 1z" fill="#9b1b2a"/><path d="M6 9v8M3 19h6" stroke="#333" stroke-width="1.2" fill="none"/></svg></div>
      </div>
    </article>
  </section>

</main>
</body>
</html>
```